SaaS Early tech startup business card design

Unique design for experience ecommerce platform company. the business cards will be used by executive members. conformance with color code is required.

```html
<!DOCTYPE html>
<html lang="en">
<head>
<meta charset="utf-8">
<title>Velto — Business Card</title>
<link rel="stylesheet" href="https://fonts.googleapis.com/css2?family=Montserrat:wght@400;500;700;800&display=swap">
<style>
  :root {
    --backdrop: #3b3c3d;
    --card-white: #ffffff;
    --navy: #17618e;
    --ink: #1f2a33;
    --teal-deep: #13729a;
    --teal: #07849a;
    --green: #0bbb9c;
    --divider: #1bb597;
  }
  * { box-sizing: border-box; margin: 0; padding: 0; }
  html, body { width: 1200px; height: 1059px; overflow: hidden; }
  body {
    background: var(--backdrop);
    font-family: "Montserrat", sans-serif;
    position: relative;
  }
  .card {
    position: absolute;
    width: 690px;
    height: 392px;
    border-radius: 16px;
    overflow: hidden;
  }
  .card-front { left: 256px; top: 100px; background: var(--card-white); }
  .card-back {
    left: 253px; top: 537px; width: 694px; height: 394px;
    background: linear-gradient(35deg, #1a6490 0%, #16688f 35%, var(--teal) 52%, #17a29a 75%, var(--green) 100%);
    display: flex; align-items: center; justify-content: center;
  }
  .brand-name {
    font-weight: 800;
    letter-spacing: -2px;
    line-height: 1;
  }
  .card-front .brand-name {
    position: absolute;
    right: 48px; top: 58px;
    font-size: 92px;
    color: var(--teal-deep);
  }
  .card-back .brand-name {
    font-size: 150px;
    color: #ffffff;
    margin-top: -10px;
  }
  .person { position: absolute; left: 29px; top: 200px; }
  .person-name {
    font-size: 23px; font-weight: 700; letter-spacing: 2px;
    color: var(--navy); text-transform: uppercase; line-height: 1.1;
  }
  .person-role { font-size: 16px; color: var(--ink); font-weight: 400; margin-top: 1px; }
  .contact-list {
    position: absolute; left: 29px; top: 281px; list-style: none;
  }
  .contact-list li {
    display: flex; align-items: center; height: 21px;
    font-size: 16px; color: var(--ink);
  }
  .contact-list svg { width: 12px; height: 12px; margin-right: 7px; fill: var(--navy); flex: none; }
  .divider {
    position: absolute; left: 291px; top: 315px; width: 1.5px; height: 48px;
    background: var(--divider);
  }
  .address {
    position: absolute; left: 313px; top: 322px;
    font-size: 16px; line-height: 21px; color: var(--ink); font-style: normal;
  }
  .color-band {
    position: absolute; left: 0; right: 0; bottom: 0; height: 9px; display: flex;
  }
  .color-band span { flex: 1; }
</style>
</head>
<body>
  <section class="card card-front">
    <div class="brand-name">velto</div>

    <div class="person">
      <h1 class="person-name">Marcus Hale</h1>
      <p class="person-role">Managing Director</p>
    </div>

    <ul class="contact-list">
      <li>
        <svg viewBox="0 0 24 24"><path d="M6.6 10.8a15.1 15.1 0 0 0 6.6 6.6l2.2-2.2c.3-.3.7-.4 1-.2 1.1.4 2.3.6 3.6.6.6 0 1 .4 1 1V20c0 .6-.4 1-1 1C10.6 21 3 13.4 3 4c0-.6.4-1 1-1h3.5c.6 0 1 .4 1 1 0 1.3.2 2.5.6 3.6.1.3 0 .7-.2 1z"/></svg>
        02 5550 1184
      </li>
      <li>
        <svg viewBox="0 0 24 24"><path d="M7 1h10a2 2 0 0 1 2 2v18a2 2 0 0 1-2 2H7a2 2 0 0 1-2-2V3a2 2 0 0 1 2-2zm0 3v14h10V4zm5 15.5a1.2 1.2 0 1 0 0 2.4 1.2 1.2 0 0 0 0-2.4z"/></svg>
        0400 555 762
      </li>
      <li>
        <svg viewBox="0 0 24 24"><path d="M2 4h20v16H2zm2.5 2v.4L12 12l7.5-5.6V6zm0 2.9V18h15V8.9L12 14.5z"/></svg>
        hello@veltoapp.com.au
      </li>
      <li>
        <svg viewBox="0 0 24 24"><path d="M12 2a10 10 0 1 0 0 20 10 10 0 0 0 0-20zm-1 17.9A8 8 0 0 1 4.2 10L9 14.8v1a2 2 0 0 0 2 2zm6.9-2.5A2 2 0 0 0 16 16h-1v-3a1 1 0 0 0-1-1H8v-2h2a1 1 0 0 0 1-1V7h2a2 2 0 0 0 2-2v-.4a8 8 0 0 1 2.9 12.8z"/></svg>
        www.veltoapp.com
      </li>
    </ul>

    <div class="divider"></div>

    <address class="address">
      Harlow Street, Suite 4<br>
      Northbridge Park, 2063
    </address>

    <div class="color-band">
      <span style="background:#17618e"></span>
      <span style="background:#13729a"></span>
      <span style="background:#1687a4"></span>
      <span style="background:#2290ac"></span>
      <span style="background:#4bbf9f"></span>
      <span style="background:#2bbc9a"></span>
      <span style="background:#13b593"></span>
      <span style="background:#1bb597"></span>
    </div>
  </section>

  <section class="card card-back">
    <div class="brand-name">velto</div>
  </section>
</body>
</html>
```